Fresh, modern, fun business card for pediatric dental practice

Need a business card for fresh, modern, fun pediatric dental practice

Clean look that matches our website's font and colors

We prefer the look of curved corners on business cards

Target Market(s)

parents (mothers) of young children, professionals, mid-high class

Industry/Entity Type

Dental

Contact Information for Business Card

Maplebrook Pediatric Dentistry
482 Quarry Lane
Suite 517
Fernwick, OR 97410
541.555.0193
www.maplebrookkidsdental.example

Mei-Ran Tsai, DMD
Corinne Walbeck, DMD
(we are working on our email address, but we would like that on the card as well)

Font styles to use
Sans Serif

Requirements
Must have
• All info; we would also like to make cards for individual staff members
• colors from our website and color palatte, attatched
• use same font and design as website for branding
Nice to have
• clean, simple card that has a pop of color
• we would like to see a few designs with our tag line "where smiles get brighter"
• we are not sure if we want to have it on there or not
• we would like to see a few designs incorporating the ribbon graphic on our website where the word WELCOME is

```html
<!DOCTYPE html>
<html lang="en">
<head>
<meta charset="utf-8">
<title>Maplebrook Pediatric Dentistry – Business Card</title>
<link href="https://fonts.googleapis.com/css2?family=Lato:wght@400;700&family=Oswald:wght@500&display=swap" rel="stylesheet">
<style>
  :root {
    --bg: #1c1c1c;
    --card: #242424;
    --yellow: #f6b92b;
    --magenta: #d6378f;
    --white: #f2f2f2;
    --muted: #cfcfcf;
  }
  * { box-sizing: border-box; margin: 0; padding: 0; }
  html, body {
    width: 1200px; height: 900px; overflow: hidden;
    background: var(--bg);
    font-family: "Lato", sans-serif;
  }
  .stage {
    width: 1200px; height: 900px;
    display: flex; flex-direction: column; align-items: center;
    justify-content: center; gap: 30px;
  }
  .card {
    position: relative;
    width: 700px; height: 400px;
    background: var(--card);
    border-radius: 22px;
    overflow: hidden;
  }
  /* front */
  .card-front {
    display: flex; flex-direction: column; align-items: center; justify-content: center;
  }
  .brand-mark {
    width: 26px; height: 26px; border-radius: 50%;
    background: var(--yellow); margin-bottom: 16px;
  }
  .brand-name {
    color: var(--yellow); font-weight: 700;
    font-size: 52px; line-height: 1; letter-spacing: 3px;
    text-transform: lowercase;
  }
  .brand-sub {
    color: var(--magenta); font-weight: 400;
    font-size: 24px; letter-spacing: 4px; margin-top: 6px;
    text-transform: lowercase;
  }
  .front-url {
    margin-top: 42px; color: var(--white);
    font-size: 17px; letter-spacing: 2px;
  }
  .front-url .accent { color: var(--yellow); }
  /* back */
  .person {
    position: absolute; left: 60px; top: 150px; width: 265px; text-align: right;
  }
  .person-name {
    font-family: "Oswald", sans-serif; font-weight: 500;
    color: var(--yellow); font-size: 32px; letter-spacing: 1px;
    text-transform: uppercase; line-height: 1.1; text-align: left;
    white-space: nowrap;
  }
  .person-title { color: var(--muted); font-size: 18px; margin-top: 4px; letter-spacing: 1px; }
  .divider {
    position: absolute; left: 345px; top: 165px;
    width: 2px; height: 70px; background: var(--magenta);
  }
  .contacts {
    position: absolute; left: 365px; top: 162px;
    list-style: none; color: var(--white); font-size: 15px;
  }
  .contacts li { display: flex; align-items: center; gap: 10px; height: 26px; white-space: nowrap; }
  .contacts svg { width: 13px; height: 13px; flex: none; }
  .practice {
    position: absolute; left: 60px; bottom: 54px;
  }
  .practice-name {
    color: var(--yellow); font-weight: 700; font-size: 19px;
    letter-spacing: 1px; text-transform: uppercase;
  }
  .practice-address { color: var(--white); font-size: 19px; margin-top: 4px; }
</style>
</head>
<body>
<main class="stage">
  <section class="card card-front">
    <div class="brand-mark"></div>
    <div class="brand-name">Maplebrook</div>
    <div class="brand-sub">Pediatric Dentistry</div>
    <div class="front-url">www.<span class="accent">maplebrookkidsdental</span>.example</div>
  </section>

  <section class="card card-back">
    <div class="person">
      <div class="person-name">Corinne Walbeck</div>
      <div class="person-title">DMD</div>
    </div>
    <div class="divider"></div>
    <ul class="contacts">
      <li>
        <svg viewBox="0 0 24 24" aria-hidden="true"><path fill="var(--yellow)" d="M6.6 10.8a15 15 0 0 0 6.6 6.6l2.2-2.2a1 1 0 0 1 1-.25 11.4 11.4 0 0 0 3.6.57 1 1 0 0 1 1 1V20a1 1 0 0 1-1 1A17 17 0 0 1 3 4a1 1 0 0 1 1-1h3.5a1 1 0 0 1 1 1c0 1.25.2 2.45.57 3.57a1 1 0 0 1-.25 1z"/></svg>
        541.555.0193
      </li>
      <li>
        <svg viewBox="0 0 24 24" aria-hidden="true"><rect x="2" y="5" width="20" height="14" rx="1" fill="var(--yellow)"/><path d="M2 6l10 7 10-7" fill="none" stroke="var(--card)" stroke-width="2"/></svg>
        info@maplebrookkidsdental.example
      </li>
      <li>
        <svg viewBox="0 0 24 24" aria-hidden="true"><g fill="none" stroke="var(--yellow)" stroke-width="2"><circle cx="12" cy="12" r="9"/><ellipse cx="12" cy="12" rx="4" ry="9"/><path d="M3 12h18M5 7h14M5 17h14"/></g></svg>
        www.maplebrookkidsdental.example
      </li>
    </ul>
    <div class="practice">
      <div class="practice-name">Maplebrook Pediatric Dentistry</div>
      <div class="practice-address">482 Quarry Lane Suite 517 Fernwick, OR 97410</div>
    </div>
  </section>
</main>
</body>
</html>
```